Business card design for modern PanoWalk agency

Hello,

I need a business card design for my company Kites7Market.
We mainly offer Zorvex PanoWalk Tours (360° Photography) and it should be a business card with following details:

Name: Tobias Wendler
Number: +49 176 58 20 917
Mail: tobias@kites7market.com
website: kites7market.com

Main colour that we use is the red of the logo.
It´s also important to integrate the "Zorvex Verified logo" as the person on this business card is a Zorvex verified photographer.

And if possible we would also like to integrate something like send us a sms or chatlink and we call you back. As the number is german but we sell now in Vienna, Austria.

We offer a good price but very high photography quality, as we are mostly students - that´s our concept.

Maybe an idea is to integrate something 360° on the back-side of the card, for example the photo attached (just an idea) or some great design.
See flyer (attached) and kites7market.com for inspiration, maybe use of the photo of me (attached) in a circle or something

I´m very excited for your designs and thanks a lot in advance!! :)

Target Market(s)

Shops, hotels, shopping centers, etc. in Vienna, Austria

Industry/Entity Type

Business

Contact Information for Business Card

double-sided, use red of the logo, 360° zorvex pano walk certified photographer

Font styles to use
Serif
Sans Serif

Colors
ec1f27

Requirements
Nice to have
• maybe some 360° design on back-side
• maybe include photo of me in a circle or something or sketched in red colour

```html
<!DOCTYPE html>
<html lang="en">
<head>
<meta charset="utf-8">
<title>Kites7Market – Business Card</title>
<link rel="stylesheet" href="https://fonts.googleapis.com/css2?family=Oswald:wght@400;500;600&family=Open+Sans:wght@400;600&display=swap">
<style>
  :root {
    --brand-red: #ec1f27;
    --brand-red-dark: #c8141c;
    --panel-grey: #a7a9ac;
    --ink-grey: #8a8c8f;
    --paper: #ffffff;
    --backdrop: #e9e6e1;
    --photo-warm: #b98a5e;
    --photo-dark: #4a3024;
    --photo-light: #e8d6bf;
  }
  * { box-sizing: border-box; margin: 0; padding: 0; }
  html, body { width: 1200px; height: 950px; overflow: hidden; }
  body {
    background: var(--backdrop);
    font-family: "Open Sans", Arial, sans-serif;
    position: relative;
  }
  .card {
    position: absolute;
    left: 260px;
    width: 680px;
    height: 410px;
    overflow: hidden;
    border-radius: 4px;
    box-shadow: 0 10px 28px rgba(0,0,0,.18);
    background: var(--paper);
  }
  .card--front { top: 45px; }
  .card--back { top: 495px; }

  /* front */
  .brand {
    position: absolute;
    top: 70px;
    right: 70px;
    display: flex;
    align-items: center;
    gap: 16px;
  }
  .brand__mark {
    width: 58px;
    height: 58px;
    background: var(--brand-red);
  }
  .brand__name {
    font-family: "Oswald", "Arial Narrow", sans-serif;
    font-weight: 500;
    font-size: 46px;
    letter-spacing: 1px;
    text-transform: uppercase;
    color: var(--ink-grey);
    line-height: 1;
  }
  .contact-panel {
    position: absolute;
    left: 0;
    bottom: 0;
    width: 385px;
    height: 175px;
    background: linear-gradient(180deg, var(--brand-red), var(--brand-red-dark));
    color: var(--paper);
    padding: 46px 0 0 190px;
  }
  .contact-panel__name {
    font-family: "Oswald", "Arial Narrow", sans-serif;
    font-weight: 600;
    font-size: 24px;
    text-transform: uppercase;
    letter-spacing: .5px;
    margin-bottom: 8px;
  }
  .contact-panel__line {
    font-size: 12px;
    line-height: 1.6;
  }
  .portrait {
    position: absolute;
    left: 40px;
    top: 175px;
    width: 150px;
    height: 150px;
    border-radius: 50%;
    border: 4px solid var(--paper);
    background: radial-gradient(circle at 50% 40%, #9aa0a4, #5e6468);
  }
  .service-panel {
    position: absolute;
    left: 385px;
    bottom: 0;
    width: 295px;
    height: 210px;
    background: var(--panel-grey);
    color: var(--paper);
    padding: 36px 24px 0 26px;
  }
  .service-panel::after {
    content: "";
    position: absolute;
    left: 0;
    right: 0;
    bottom: 0;
    height: 22px;
    background: var(--brand-red);
  }
  .service-panel__title {
    font-family: "Oswald", "Arial Narrow", sans-serif;
    font-weight: 600;
    font-size: 17px;
    text-transform: uppercase;
    line-height: 1.35;
  }
  .service-panel__note {
    margin-top: 12px;
    font-size: 12px;
    line-height: 1.5;
  }

  /* back */
  .pano {
    position: absolute;
    inset: 0;
    background:
      radial-gradient(ellipse at 72% 35%, var(--photo-light) 0%, transparent 45%),
      linear-gradient(120deg, var(--photo-dark) 0%, var(--photo-warm) 55%, var(--photo-light) 100%);
  }
  .back-brand {
    position: absolute;
    left: 50%;
    top: 50%;
    transform: translate(-50%, -50%);
    display: flex;
    align-items: center;
    gap: 18px;
    background: rgba(255,255,255,.82);
    padding: 22px 34px;
  }
  .back-brand .brand__mark { width: 62px; height: 62px; }
  .back-brand .brand__name { color: var(--brand-red); font-size: 50px; }
  .verified-badge {
    position: absolute;
    top: 26px;
    right: 26px;
    width: 120px;
    height: 56px;
    border-radius: 6px;
    background: rgba(255,255,255,.9);
  }
</style>
</head>
<body>

<section class="card card--front" aria-label="Business card front">
  <div class="brand">
    <span class="brand__mark"></span>
    <span class="brand__name">Kites7Market</span>
  </div>

  <div class="contact-panel">
    <p class="contact-panel__name">Tobias Wendler</p>
    <p class="contact-panel__line">P: +49 176 58 20 917</p>
    <p class="contact-panel__line">tobias@kites7market.com</p>
    <p class="contact-panel__line">www.kites7market.com</p>
  </div>

  <div class="portrait" role="img" aria-label="Portrait photo of Tobias Wendler"></div>

  <div class="service-panel">
    <p class="service-panel__title">360° Zorvex Pano Walk<br>Certified Photographer</p>
    <p class="service-panel__note">send us a sms or chatlink<br>and we call you back.</p>
  </div>
</section>

<section class="card card--back" aria-label="Business card back">
  <div class="pano" role="img" aria-label="360° interior photo of a warmly lit café room"></div>
  <div class="verified-badge" role="img" aria-label="Zorvex Verified badge"></div>
  <div class="back-brand">
    <span class="brand__mark"></span>
    <span class="brand__name">Kites7Market</span>
  </div>
</section>

</body>
</html>
```